I am hosting a banquet called, Copper & Pearl Gala and I need a design to help sell it on Linkora.

Hi all.
No disco balls, please.
I would like a miser-traditional design, classy.

```html
<!DOCTYPE html>
<html lang="en">
<head>
<meta charset="utf-8">
<title>Copper &amp; Pearl Gala</title>
<link rel="stylesheet" href="https://fonts.googleapis.com/css2?family=Cormorant+Garamond:wght@500;600;700&family=Playfair+Display:wght@700&family=Poppins:wght@400;500;600;700&display=swap">
<style>
  :root {
    --ink: #0b0b0b;
    --paper: #f4f1e8;
    --silver: #c9c9c9;
    --silver-dark: #7a7a7a;
    --band-mid: #9a9a9a;
    --band-edge: #161616;
    --ornament: #3a3a3a;
  }
  * { margin: 0; padding: 0; box-sizing: border-box; }
  html, body { width: 1200px; height: 1200px; overflow: hidden; background: var(--ink); }
  .invite {
    position: relative; width: 1200px; height: 1200px;
    background: var(--ink); color: var(--paper);
    font-family: "Poppins", sans-serif;
  }
  .invite > * { position: absolute; }
  .frames { left: 0; top: 0; width: 1200px; height: 1200px; }
  .center { left: 0; width: 1200px; text-align: center; }
  .pattern-left, .pattern-right {
    top: 240px; width: 260px; height: 700px; border-radius: 50%;
    background: radial-gradient(ellipse at center, #2a2a2a 0%, #161616 55%, rgba(11,11,11,0) 75%);
  }
  .pattern-left { left: 30px; }
  .pattern-right { right: 30px; }
  .pattern-bottom {
    left: 330px; top: 900px; width: 540px; height: 160px; border-radius: 50%;
    background: radial-gradient(ellipse at center, #222 0%, rgba(11,11,11,0) 70%);
  }
  .ornament {
    background: radial-gradient(ellipse at center, #bdbdbd 0%, #6d6d6d 55%, rgba(60,60,60,0) 80%);
    border-radius: 50%;
  }
  .orn-top { left: 558px; top: 22px; width: 90px; height: 46px; }
  .orn-bottom { left: 558px; top: 1132px; width: 90px; height: 46px; }
  .orn-left { left: 15px; top: 552px; width: 56px; height: 90px; }
  .orn-right { left: 1129px; top: 552px; width: 56px; height: 90px; }
  .divider-flourish { left: 494px; top: 400px; width: 228px; height: 34px; }
  .event-series {
    top: 206px; font-family: "Playfair Display", serif; font-weight: 700;
    font-size: 34px; letter-spacing: 2.5px;
  }
  .event-title {
    top: 314px; font-family: "Cormorant Garamond", serif; font-weight: 600;
    font-size: 78px; line-height: 1;
    transform: translateY(-50%);
  }
  .event-title span {
    background: linear-gradient(180deg, #9e9e9e 0%, #f2f2f2 38%, #8a8a8a 62%, #d8d8d8 100%);
    -webkit-background-clip: text; background-clip: text; color: transparent;
  }
  .tagline {
    left: 382px; top: 495px; width: 469px; height: 33px;
    border-top: 1px solid var(--silver); border-bottom: 1px solid var(--silver);
    text-align: center; font-weight: 600; font-size: 16px; letter-spacing: 5.8px;
    line-height: 31px; padding-left: 5.8px;
  }
  .event-date {
    top: 553px; font-family: "Cormorant Garamond", serif; font-weight: 500;
    font-size: 60px; line-height: 1; letter-spacing: 1px;
    font-variant-numeric: lining-nums;
  }
  .schedule-band {
    left: 0; top: 669px; width: 1200px; height: 105px;
    background: linear-gradient(90deg, var(--band-edge) 0%, #3a3a3a 16%, #6a6a6a 34%, var(--band-mid) 50%, #6a6a6a 66%, #3a3a3a 84%, var(--band-edge) 100%);
  }
  .schedule-band .cell {
    position: absolute; top: 0; height: 105px; display: flex; flex-direction: column;
    justify-content: center; align-items: center; font-size: 26px; line-height: 1.25;
  }
  .cell-social { left: 200px; width: 226px; }
  .cell-day {
    left: 426px; width: 329px; font-size: 40px !important; font-weight: 400;
    background: linear-gradient(90deg, #858585, #9e9e9e 50%, #858585);
    border-left: 1px solid #2a2a2a; border-right: 1px solid #2a2a2a;
  }
  .cell-dinner { left: 755px; width: 225px; }
  .venue-name { top: 822px; font-size: 23px; letter-spacing: 2.8px; }
  .venue-address { top: 852px; font-size: 19px; }
  .dress-label {
    left: 82px; top: 1013px; font-weight: 700; font-size: 43px; line-height: 49px;
  }
  .dress-detail { left: 241px; top: 1018px; font-size: 24.5px; line-height: 31.5px; }
  .rsvp { left: 708px; top: 984px; font-size: 28px; line-height: 1.2; }
  .rsvp-date { left: 708px; top: 1020px; font-size: 31px; line-height: 1.2; }
  .ticket { left: 708px; top: 1064px; font-size: 41px; line-height: 1.2; }
  .ticket strong { font-weight: 700; }
</style>
</head>
<body>
<main class="invite">
  <div class="pattern-left" role="img" aria-label="Faint ornamental mandala pattern"></div>
  <div class="pattern-right" role="img" aria-label="Faint ornamental mandala pattern"></div>
  <div class="pattern-bottom" role="img" aria-label="Faint ornamental mandala pattern"></div>

  <svg class="frames" viewBox="0 0 1200 1200" aria-hidden="true">
    <defs>
      <linearGradient id="silverLine" x1="0" x2="1">
        <stop offset="0" stop-color="#777"/>
        <stop offset="0.5" stop-color="#d6d6d6"/>
        <stop offset="1" stop-color="#777"/>
      </linearGradient>
    </defs>
    <rect x="43" y="43" width="1072" height="1072" fill="none" stroke="url(#silverLine)" stroke-width="3" stroke-dasharray="120 8 10 8"/>
    <path d="M 284 137 L 553 137 Q 580 137 597 104 Q 614 137 641 137 L 930 137 Q 971 137 971 178 L 971 374 Q 971 400 1002 414 Q 969 428 968 456 L 968 910 Q 968 948 930 948 L 641 948 Q 614 948 597 981 Q 580 948 553 948 L 284 948 Q 246 948 246 910 L 246 456 Q 245 428 214 414 Q 243 400 243 374 L 243 178 Q 243 137 284 137 Z"
      fill="#0b0b0b" stroke="var(--paper)" stroke-width="2.5"/>
  </svg>

  <div class="ornament orn-top" role="img" aria-label="Silver filigree ornament"></div>
  <div class="ornament orn-bottom" role="img" aria-label="Silver filigree ornament"></div>
  <div class="ornament orn-left" role="img" aria-label="Silver filigree ornament"></div>
  <div class="ornament orn-right" role="img" aria-label="Silver filigree ornament"></div>

  <p class="center event-series">Marrowfield Centennial</p>
  <h1 class="center event-title"><span>Copper &amp; Pearl Gala</span></h1>
  <div class="ornament divider-flourish" role="img" aria-label="Silver scroll flourish divider"></div>
  <p class="tagline">JOIN US FOR THE CELEBRATION</p>
  <p class="center event-date">JUNE 3, 2023</p>

  <section class="schedule-band">
    <div class="cell cell-social"><span>Social Hour</span><span>6:00 p.m.</span></div>
    <div class="cell cell-day">SATURDAY</div>
    <div class="cell cell-dinner"><span>Dinner</span><span>7:00 p.m.</span></div>
  </section>

  <p class="center venue-name">MARROWFIELD HIGH SCHOOL GYMNASIUM</p>
  <p class="center venue-address">214 Alder Street, Marrowfield, Kansas</p>

  <p class="dress-label">DRESS<br>CODE</p>
  <p class="dress-detail">Black &amp; White Attire<br>Smart Casual to<br>Fancy Formal</p>

  <p class="rsvp">RSVP</p>
  <p class="rsvp-date">Monday, May 29, 2023</p>
  <p class="ticket">TICKET PRICE <strong>$30</strong></p>
</main>
</body>
</html>
```